Duct Manufacturing Company new to the industry needs business card and stationary design

we are sheet metal duct manufacturers looking for a business card design to fit my new business logo.
nothing to crazy that will date, but want it to stand out from the crowed.
I'm sure you guys will work it out.

Contact Information for Business Card

Glen Marsh
Director

Address
17 Dorwell St
Merrivale NSW 2741

0438 760 514

Sales@flowbend.com.au

Font styles to use
Other font styles liked:
• BankGothic md bt

Requirements
Nice to have
• Like the idea of corner rounded to match logo
• like to keep colours flowing
• font I like sharp square not rounded

```html
<!DOCTYPE html>
<html lang="en">
<head>
<meta charset="utf-8">
<title>Flowbend Industries – Business Card</title>
<link rel="stylesheet" href="https://fonts.googleapis.com/css2?family=Michroma&family=Montserrat:wght@400;500&display=swap">
<style>
  :root {
    --backdrop: #a9a9a9;
    --card: #141517;
    --brand-blue: #1b6fc2;
    --brand-green: #7ac943;
    --text-light: #f2f2f2;
  }
  * { margin: 0; padding: 0; box-sizing: border-box; }
  html, body { width: 1200px; height: 1200px; overflow: hidden; }
  body {
    background: var(--backdrop);
    position: relative;
    font-family: "Montserrat", Arial, sans-serif;
  }
  .card {
    position: absolute;
    width: 714px;
    height: 420px;
    background: var(--card);
    border-radius: 28px;
  }
  .card--front { left: 238px; top: 117px; }
  .card--back { left: 231px; top: 642px; }

  .brand {
    position: absolute;
    display: flex;
    flex-direction: column;
    align-items: center;
    gap: 16px;
  }
  .brand__dot {
    width: 60px;
    height: 60px;
    border-radius: 50%;
    background: var(--brand-green);
  }
  .brand__name {
    font-family: "Michroma", "Arial Black", sans-serif;
    color: var(--brand-green);
    font-size: 28px;
    line-height: 1.35;
    letter-spacing: 2px;
    text-align: center;
  }
  .card--front .brand { left: 0; right: 0; top: 132px; }
  .card--back .brand { left: 50px; width: 300px; top: 138px; }
  .card--back .brand__name { font-size: 23px; }

  .contact {
    position: absolute;
    left: 400px;
    top: 112px;
    color: var(--text-light);
  }
  .contact__name {
    font-family: "Michroma", "Arial Black", sans-serif;
    color: var(--brand-blue);
    font-size: 21px;
    letter-spacing: 2px;
    line-height: 1;
  }
  .contact__role {
    font-size: 17px;
    margin-top: 10px;
    margin-bottom: 22px;
  }
  .contact__list { list-style: none; }
  .contact__item {
    display: flex;
    align-items: center;
    gap: 16px;
    font-size: 18px;
    height: 25px;
  }
  .contact__icon { width: 16px; height: 16px; flex: none; }
  .contact__address {
    font-style: normal;
    font-size: 18px;
    line-height: 22px;
    margin-top: 6px;
  }
</style>
</head>
<body>
  <section class="card card--front">
    <div class="brand">
      <span class="brand__dot"></span>
      <p class="brand__name">FLOWBEND<br>INDUSTRIES</p>
    </div>
  </section>

  <section class="card card--back">
    <div class="brand">
      <span class="brand__dot"></span>
      <p class="brand__name">FLOWBEND<br>INDUSTRIES</p>
    </div>

    <div class="contact">
      <h1 class="contact__name">GLEN MARSH</h1>
      <p class="contact__role">Director</p>
      <ul class="contact__list">
        <li class="contact__item">
          <svg class="contact__icon" viewBox="0 0 16 16" aria-hidden="true">
            <path fill="var(--brand-blue)" d="M1 5c0-2 3-3 7-3s7 1 7 3v1h-3V4.5C11 4 5 4 4 4.5V6H1z M4 7h8l2 6v1H2v-1z"/>
            <circle cx="8" cy="10" r="1.8" fill="var(--card)"/>
          </svg>
          <span>0438 760 514</span>
        </li>
        <li class="contact__item">
          <svg class="contact__icon" viewBox="0 0 16 16" aria-hidden="true" fill="none" stroke="var(--brand-blue)" stroke-width="1.4">
            <circle cx="8" cy="8" r="6.3"/>
            <ellipse cx="8" cy="8" rx="2.8" ry="6.3"/>
            <path d="M1.7 8h12.6M2.6 5h10.8M2.6 11h10.8"/>
          </svg>
          <span>flowbend.com.au</span>
        </li>
        <li class="contact__item">
          <svg class="contact__icon" viewBox="0 0 16 16" aria-hidden="true">
            <rect x="1" y="3" width="14" height="10" fill="var(--brand-blue)"/>
            <path d="M1 3l7 6 7-6M1 13l5-5M15 13l-5-5" fill="none" stroke="var(--card)" stroke-width="1.2"/>
          </svg>
          <span>Sales@flowbend.com.au</span>
        </li>
      </ul>
      <address class="contact__address">17 Dorwell St<br>Merrivale NSW 2741</address>
    </div>
  </section>
</body>
</html>
```